Automotive component supplier needs a business card design

We need a business card design for our company called Velran Global Components Ltd based in the UK. We are a supplier of interior and exterior components to premium car manufacturers such as Corvel Ashby, Hadley Fenn, Marquist and Tavarelli. We would like to see a modern business card design that uses the colour blue.

Target Market(s)

Premium automotive car manufacturers.

Industry/Entity Type

Automotive

Contact Information for Business Card

Company Name : Velran Global Components Limited
Address: 17 Marlow Yard, Upper Heath, Warwick, CV31 8QL, United Kingdom
Web Address : www.velrancomponents-example.co.uk

Font styles to use
Other font styles liked:
• Helvetica

Colors
3176b5
0255a3
85acd3
cfdeed
cee9f5
85cae6
34a6d7
0692cd
9bcb3c

Requirements
Must have
• Clear company logo and a mixture of blue colours.
Nice to have
• A high quality modern image.
Should not have
• Multiple colours.

```html
<!DOCTYPE html>
<html lang="en">
<head>
<meta charset="utf-8">
<title>Velran Global Components – Business Card</title>
<link rel="stylesheet" href="https://fonts.googleapis.com/css2?family=Arimo:wght@400;700&family=Michroma&display=swap">
<style>
  :root {
    --backdrop: #3a3a3c;
    --card: #020304;
    --blue: #1e9ad8;
    --blue-deep: #0692cd;
    --green: #9bcb3c;
    --text-font: "Arimo", Helvetica, Arial, sans-serif;
    --name-font: "Michroma", "Arimo", sans-serif;
  }
  * { margin: 0; padding: 0; box-sizing: border-box; }
  html, body {
    width: 1200px; height: 900px; overflow: hidden;
    background: var(--backdrop);
  }
  .stage { position: relative; width: 1200px; height: 900px; }
  .card {
    position: absolute; width: 600px; height: 343px;
    background: var(--card);
    box-shadow: 0 10px 30px rgba(0,0,0,.45);
    font-family: var(--text-font);
  }
  .card--front { left: 120px; top: 80px; }
  .card--back { left: 480px; top: 480px; }

  .wordmark {
    display: flex; align-items: center; gap: 10px;
    color: var(--blue);
    font-family: var(--text-font); font-weight: 700;
    text-transform: uppercase; letter-spacing: 1px;
  }
  .wordmark__square {
    width: 14px; height: 14px; border-radius: 3px; background: var(--green);
  }
  .card--front .wordmark {
    position: absolute; left: 0; right: 0; top: 140px;
    justify-content: center; font-size: 28px;
  }
  .card--front .website {
    position: absolute; right: 48px; bottom: 40px;
    color: var(--blue); font-size: 14px;
  }

  .card--back .wordmark {
    position: absolute; left: 34px; top: 92px; font-size: 22px;
  }
  .person { position: absolute; left: 34px; top: 160px; }
  .person__name {
    color: var(--blue); font-family: var(--name-font);
    font-size: 17px; letter-spacing: 2px; text-transform: uppercase;
  }
  .person__role { color: var(--green); font-size: 14px; margin-top: 6px; }
  .divider {
    position: absolute; left: 112px; right: 0; top: 200px;
    height: 1px; background: var(--green);
  }
  .address {
    position: absolute; left: 34px; top: 216px;
    color: var(--blue); font-size: 14px; line-height: 18px;
  }
  .contacts {
    position: absolute; left: 34px; top: 260px; list-style: none;
    color: var(--blue); font-size: 14px; line-height: 18px;
  }
  .contacts li { display: flex; align-items: center; gap: 10px; }
  .contacts svg { width: 11px; height: 11px; fill: var(--green); flex: none; }
</style>
</head>
<body>
<main class="stage">
  <section class="card card--front" aria-label="Card front">
    <div class="wordmark"><span class="wordmark__square"></span>Velran Global Components</div>
    <div class="website">www.velrancomponents-example.co.uk</div>
  </section>

  <section class="card card--back" aria-label="Card back">
    <div class="wordmark"><span class="wordmark__square"></span>Velran Global Components</div>
    <div class="divider"></div>
    <div class="person">
      <div class="person__name">Dara Whitlock</div>
      <div class="person__role">Director</div>
    </div>
    <div class="address">17 Marlow Yard, Upper Heath<br>Warwick, CV31 8QL, UK</div>
    <ul class="contacts">
      <li><svg viewBox="0 0 24 24"><path d="M6.6 10.8a15 15 0 0 0 6.6 6.6l2.2-2.2c.3-.3.7-.4 1-.2 1.1.4 2.3.6 3.6.6.6 0 1 .4 1 1V20c0 .6-.4 1-1 1A17 17 0 0 1 3 4c0-.6.4-1 1-1h3.5c.6 0 1 .4 1 1 0 1.3.2 2.5.6 3.6.1.3 0 .7-.2 1z"/></svg>780 555-0142</li>
      <li><svg viewBox="0 0 24 24"><path d="M7 1h10a2 2 0 0 1 2 2v18a2 2 0 0 1-2 2H7a2 2 0 0 1-2-2V3a2 2 0 0 1 2-2zm0 3v14h10V4zm5 15.5a1 1 0 1 0 0 2 1 1 0 0 0 0-2z"/></svg>780 555-0187</li>
      <li><svg viewBox="0 0 24 24"><path d="M2 5h20v14H2zm2 2v.5l8 5 8-5V7l-8 5z"/></svg>velranparts@example.com</li>
      <li><svg viewBox="0 0 24 24"><circle cx="12" cy="12" r="10"/></svg>www.velrancomponents-example.co.uk</li>
    </ul>
  </section>
</main>
</body>
</html>
```